We are a recruitment company based in Norwich/Cambridge England.
I have included our company logo which we want to remain the same.

What we are looking for is a new creative Business card which will really stand out!!

Contact Information for Business Card

Harriet Dunmore
email: Harriet@plavex.co.uk
Address: Brackwell House
Fenmoor Enterprise Park
Partridge Way
Norwich
QB9 3KX
Tel:01632 960418

```html
<!DOCTYPE html>
<html lang="en">
<head>
<meta charset="utf-8">
<title>Plavex Business Card</title>
<link rel="stylesheet" href="https://fonts.googleapis.com/css2?family=Lato:wght@400;700&display=swap">
<style>
  :root {
    --backdrop: #2a2a2a;
    --card: #f3f3f3;
    --green: #8cc63f;
    --grey: #8a878c;
    --ink: #555555;
    --muted: #8a8a8a;
  }
  html, body {
    margin: 0;
    width: 1200px;
    height: 960px;
    overflow: hidden;
    background: var(--backdrop);
    font-family: "Lato", Arial, sans-serif;
  }
  .card {
    position: absolute;
    width: 600px;
    height: 343px;
    background: var(--card);
    border-radius: 22px;
    overflow: hidden;
    box-shadow: 0 3px 8px rgba(0,0,0,0.45);
  }
  .card-front { left: 314px; top: 113px; }
  .card-back  { left: 311px; top: 472px; }

  .accent-band-green, .accent-band-grey { position: absolute; top: 0; bottom: 0; }
  .card-front .accent-band-grey  { right: 0; width: 64px; background: var(--grey); }
  .card-front .accent-band-green { right: 64px; width: 22px; background: var(--green); }
  .card-back .accent-band-green  { left: 0; width: 64px; background: var(--green); }
  .card-back .accent-band-grey   { left: 64px; width: 22px; background: var(--grey); }

  .holder-name {
    position: absolute; left: 59px; top: 66px; margin: 0;
    font-size: 22px; font-weight: 700; color: var(--green); text-transform: uppercase; letter-spacing: 0.3px;
  }
  .holder-role {
    position: absolute; left: 59px; top: 94px; margin: 0;
    font-size: 15px; color: var(--muted); text-transform: uppercase;
  }
  .address {
    position: absolute; left: 59px; top: 128px; margin: 0;
    font-size: 15px; line-height: 19px; color: var(--ink); font-style: normal;
  }
  .contact-list {
    position: absolute; left: 59px; top: 178px; margin: 0; padding: 0; list-style: none;
    font-size: 15px; line-height: 19px; color: var(--ink);
  }
  .contact-list li { display: flex; align-items: center; gap: 9px; }
  .contact-list svg { width: 14px; height: 14px; fill: var(--green); flex: none; }

  .brand {
    position: absolute; left: 272px; top: 120px;
    display: flex; align-items: center; gap: 14px;
  }
  .brand-dot { width: 40px; height: 40px; border-radius: 50%; background: var(--grey); }
  .brand-name { font-size: 44px; font-weight: 700; color: var(--green); line-height: 1; }
  .brand-tagline {
    position: absolute; left: 380px; top: 188px; margin: 0;
    font-size: 8px; letter-spacing: 2.4px; color: var(--muted);
  }
</style>
</head>
<body>
  <section class="card card-front">
    <div class="accent-band-green"></div>
    <div class="accent-band-grey"></div>
    <h1 class="holder-name">Harriet Dunmore</h1>
    <p class="holder-role">CEO/Founder</p>
    <address class="address">Brackwell House, Partridge Way<br>Norwich QB9 3KX</address>
    <ul class="contact-list">
      <li><svg viewBox="0 0 16 16"><path d="M3 1l3 3-2 2c1 2 4 5 6 6l2-2 3 3-2 2C7 15 1 9 1 3z"/></svg>01632 960418</li>
      <li><svg viewBox="0 0 16 16"><path d="M4 0h8v16H4zM5.5 2v10h5V2zM7 13h2v1.5H7z" fill-rule="evenodd"/></svg>07700 900362</li>
      <li><svg viewBox="0 0 16 16"><path d="M4 1h8v4H4zM1 6h14v6h-3v3H4v-3H1zM5 10v3h6v-3z" fill-rule="evenodd"/></svg>01632 960577</li>
      <li><svg viewBox="0 0 16 16"><path d="M1 4h14v9H1zM2 5l6 4 6-4v-.5H2z" fill-rule="evenodd"/></svg>Harriet@plavex.co.uk</li>
      <li><svg viewBox="0 0 16 16"><circle cx="8" cy="8" r="7"/></svg>www.plavex.co.uk</li>
    </ul>
  </section>

  <section class="card card-back">
    <div class="accent-band-green"></div>
    <div class="accent-band-grey"></div>
    <div class="brand">
      <span class="brand-dot"></span>
      <span class="brand-name">Plavex</span>
    </div>
    <p class="brand-tagline">Technology Recruitment</p>
  </section>
</body>
</html>
```